New Alcoholic Spiked Seltzer Line

We need a can design for a line of low calorie alcoholic seltzer. This product is a sparkling water and vodka drink with no sugar added in a slim 12 oz can.

This is a lighter, healthier, alternative to the sugary ready-to-drinks on the market. The product contains only 3 ingredients: Vodka, Water and Natural Flavors. It has only 100 calories but still has 5% alcohol, so you don't need to sacrifice alcohol to cut calories.

This product also does not contain any preservatives.

We want this design to communicate the following objectives to the consumer and in this order:

1. Appetizing product
2.Low calorie
3.Communicate the type of beverage (Spiked Seltzer)

The brand name of the product is VELKA.

The flavor of the product needed to be used for the design is Mango-Orange.

Comparable products are:

www.brindlefizzworks.example/
https://www.quorvabubbles.example
https://pelnavo.example/

The designs should not infringe or copy the creative directions of the products mentionned above. They are only given so that you can better understand the type of product we are developing.

Target Market(s)

Young Professional women between the ages of 25 and 44

Industry/Entity Type

Product

Colors

Designer to choose colors to be used in the design.

Requirements
Must have
• Design extendibility, meaning it can be adapted for other flavors.
• This is a new category in the market we are targeting, so consumers must easily be able to identify what type of product this is.

```html
<!DOCTYPE html>
<html lang="en">
<head>
<meta charset="utf-8">
<title>VELKA Spiked Seltzer – Mango Orange Label</title>
<link href="https://fonts.googleapis.com/css2?family=Montserrat:wght@300;400;600;700;800&display=swap" rel="stylesheet">
<style>
  :root {
    --stage: #eceef1;
    --mango: #ffcc00;
    --orange: #f7941d;
    --purple: #8e288e;
    --accent: #ffc20e;
    --white: #ffffff;
    --fruit-warm: #f39a1e;
    --fruit-red: #d9452b;
    --fruit-leaf: #5f8f3a;
  }
  * { box-sizing: border-box; margin: 0; padding: 0; }
  html, body {
    width: 1200px; height: 1036px; overflow: hidden;
    background: var(--stage);
    font-family: "Montserrat", sans-serif;
  }
  .label {
    position: absolute; left: 434px; top: 41px;
    width: 332px; height: 954px;
    background: var(--purple);
    overflow: hidden;
  }
  .flavor-band {
    position: absolute; left: 0; width: 100%;
    color: var(--white); font-weight: 300; font-size: 27px;
    letter-spacing: 0.5px; text-align: center;
    display: flex; align-items: center; justify-content: center;
  }
  .flavor-band--mango { top: 0; height: 40px; background: var(--mango); }
  .flavor-band--orange { top: 40px; height: 44px; background: var(--orange); }
  .flavor-icon { position: absolute; right: 22px; top: 50%; transform: translateY(-50%); }
  .fruit-photo {
    position: absolute; left: 0; top: 84px; width: 100%; height: 396px;
    background:
      radial-gradient(circle at 30% 78%, #fbb62a 0 22%, transparent 40%),
      radial-gradient(circle at 75% 55%, var(--fruit-red) 0 18%, transparent 45%),
      radial-gradient(circle at 70% 12%, var(--fruit-leaf) 0 8%, transparent 22%),
      linear-gradient(160deg, #f7b23c 0%, var(--fruit-warm) 45%, #e0632a 100%);
  }
  .brand-frame {
    position: absolute; left: 32px; top: 176px;
    width: 270px; height: 264px;
    border: 4px solid var(--white);
  }
  .brand-name {
    position: absolute; left: 0; top: 242px; width: 100%;
    text-align: center; color: var(--white);
    font-weight: 800; font-size: 66px; letter-spacing: 3px; line-height: 1;
  }
  .product-type {
    position: absolute; left: 106px; top: 500px;
    color: var(--white); font-weight: 700; font-size: 19px; letter-spacing: 0.3px;
  }
  .claim {
    position: absolute; left: 102px;
    font-weight: 400; font-size: 34px; line-height: 40px; letter-spacing: 0.3px;
  }
  .claim--calories { top: 556px; }
  .claim--alcohol { top: 704px; }
  .claim .hl { color: var(--accent); display: block; }
  .claim .base { color: var(--white); display: block; }
  .can-size {
    position: absolute; left: 30px; top: 836px;
    color: var(--white); font-size: 9px; font-weight: 600;
  }
  .sugar-note {
    position: absolute; left: 26px; top: 850px; width: 36px;
    color: var(--accent); font-size: 8px; font-weight: 700; line-height: 10px;
    text-align: right;
  }
  .ingredients {
    position: absolute; left: 106px; top: 876px;
    color: var(--white); font-size: 9px; font-weight: 700; letter-spacing: 0.2px;
  }
</style>
</head>
<body>
  <main class="label">
    <div class="flavor-band flavor-band--mango">MANGO
      <svg class="flavor-icon" width="22" height="22" viewBox="0 0 22 22" aria-hidden="true">
        <circle cx="10" cy="12" r="7" fill="none" stroke="#222" stroke-width="2"/>
      </svg>
    </div>
    <div class="flavor-band flavor-band--orange">ORANGE
      <svg class="flavor-icon" width="22" height="22" viewBox="0 0 22 22" aria-hidden="true">
        <circle cx="11" cy="12" r="7" fill="none" stroke="#222" stroke-width="2"/>
      </svg>
    </div>
    <div class="fruit-photo" role="img" aria-label="Photo of a ripe mango with green leaves and a sliced orange"></div>
    <div class="brand-frame"></div>
    <div class="brand-name">VELKA</div>
    <div class="product-type">SPIKED SELTZER</div>
    <div class="claim claim--calories">
      <span class="hl">ONE</span><span class="hl">HUNDRED</span><span class="base">CALORIES</span>
    </div>
    <div class="claim claim--alcohol">
      <span class="hl">FIVE</span><span class="hl">PERCENT</span><span class="base">ALCOHOL</span>
    </div>
    <div class="can-size">12 OZ</div>
    <div class="sugar-note">NO<br>SUGAR<br>ADDED</div>
    <div class="ingredients">VODKA, WATER, NATURAL FLAVORS</div>
  </main>
</body>
</html>
```